Korvalith Brochure Design - IT Services - Modern Design - Services List

Hi,

We are looking for a modern IT Services brochure design of between 4 - 6 pages, it must be based on a blue and white colour theme with some nice technical imagery. It would need a section about why Korvalith and a contact section at the end.

Here is some info that could be included

Target Market(s)

Medium to Large Businesses

Industry/Entity Type

Information Technology

Colors
0054AA
0677BA
7BADD7
CADEEF
E8F1F8

Requirements
Must have
• Striking technical imagery
Nice to have
• Nice Icons to list the different services sections

```html
<!DOCTYPE html>
<html lang="en">
<head>
<meta charset="utf-8">
<title>Korvalith IT Services Brochure</title>
<link rel="stylesheet" href="https://fonts.googleapis.com/css2?family=Oswald:wght@500;600;700&family=Poppins:wght@300;400;500;600;700&display=swap">
<style>
:root{
  --stage:#8eaed8;
  --paper:#ffffff;
  --ink:#1f1f1f;
  --ink-soft:#3a3a3a;
  --cyan:#1cb8f2;
  --cyan-deep:#0677ba;
  --navy:#0054aa;
  --sky:#7badd7;
  --mist:#cadeef;
  --frost:#e8f1f8;
  --ghost:#c3e4f7;
  --card-dark:#2a2b2e;
}
*{margin:0;padding:0;box-sizing:border-box}
html,body{width:1200px;height:2456px;overflow:hidden;background:var(--stage)}
body{position:relative;font-family:"Poppins",sans-serif;color:var(--ink)}
.spread{position:absolute;left:87px;width:1012px;height:715px;background:var(--paper);overflow:hidden}
.spread--cover{top:98px}
.spread--inside{top:869px}
.spread--back{top:1640px}
.abs{position:absolute}
.head{font-family:"Oswald",sans-serif;font-weight:600;line-height:1;letter-spacing:-.3px}
.cyan{color:var(--cyan)}
.ph{position:absolute}
.center{text-align:center}

/* cover spread */
.touch-title{left:102px;top:80px;width:300px;font-size:16px;font-weight:500;color:var(--cyan)}
.touch-copy{left:102px;top:110px;width:300px;font-size:11px;line-height:1.3;color:var(--ink-soft)}
.net-globe{left:28px;top:197px;width:115px;height:105px;border-radius:50%;background:radial-gradient(circle at 40% 40%,#fff,#d9dde3 55%,#3a7fe0 100%)}
.contact-title{left:152px;top:234px;width:200px;font-size:16px;font-weight:500}
.contact-list{left:102px;top:266px;width:300px;list-style:none;font-size:14px;font-weight:300;line-height:21px}
.contact-list li{display:flex;justify-content:center;gap:6px;align-items:flex-start}
.contact-list svg{flex:none;margin-top:4px}
.follow{left:171px;top:417px;display:flex;align-items:center;gap:12px;font-size:16px;font-weight:500;color:var(--cyan)}
.follow .dot{width:14px;height:14px;border-radius:50%;background:var(--ink)}
.follow .dot.blue{background:var(--cyan-deep)}
.ghost-name{left:455px;top:548px;transform-origin:0 0;transform:rotate(-90deg);font-family:"Oswald",sans-serif;font-weight:700;font-size:146px;line-height:118px;color:var(--ghost);white-space:nowrap;letter-spacing:-2px}
.skyline{left:0;top:470px;width:1012px;height:245px;background:linear-gradient(180deg,rgba(255,255,255,0) 0%,#b7d1ee 28%,#8fb6e3 62%,#6c9dd6 100%)}
.brand{left:620px;top:76px;width:280px}
.brand-name{font-family:"Poppins",sans-serif;font-weight:700;font-size:34px;color:var(--cyan-deep);letter-spacing:1px;line-height:1}
.corner-globe{left:912px;top:45px;width:110px;height:170px;border-radius:55px 0 0 55px;background:radial-gradient(circle at 45% 50%,#fff,#dfe3e8 55%,#2f7fe6 100%)}
.cover-title{left:560px;top:222px;width:400px;font-size:68px;line-height:68px;color:var(--ink)}
.cover-title span{display:block}
.tagline{left:560px;top:358px;width:400px;font-size:23px;line-height:26px;font-weight:300}
.tag-band{left:593px;top:386px;width:333px;height:40px;background:var(--ink);transform:rotate(-3deg);border-bottom:4px solid var(--cyan);color:#fff;font-size:20px;font-weight:300;line-height:36px;text-align:center}

/* inside spread */
.about-title{left:29px;top:45px;font-size:29px}
.about-copy{left:29px;top:112px;width:262px;font-size:12.4px;line-height:15.4px;color:var(--ink-soft)}
.about-frame{left:298px;top:46px;width:180px;height:196px;background:var(--cyan);transform:rotate(-2deg)}
.about-photo{left:304px;top:48px;width:178px;height:196px;background:linear-gradient(135deg,#e8e9ec,#c7c9cd 60%,#9ea3aa)}
.services-title{left:29px;top:284px;font-size:29px}
.rule-v{width:1px;background:#555}
.managed{left:147px;top:300px;font-size:16.5px;line-height:19px}
.managed-copy{left:257px;top:282px;width:215px;font-size:9.8px;line-height:11.6px}
.svc{position:absolute;width:138px;height:134px;border:1px solid #333;border-radius:4px;padding:14px 14px 0 14px;background:#fff}
.svc.blue{border-color:var(--cyan)}
.svc h4{font-size:11.5px;font-weight:400;line-height:14px;margin-top:6px}
.svc p{font-size:9.5px;line-height:11px;color:var(--ink-soft);margin-top:4px}
.mid-brand{left:185px;top:422px;width:135px;text-align:center}
.mid-brand .brand-name{font-size:19px}
.arrow{position:absolute}
.cloud-photo{left:533px;top:34px;width:196px;height:331px;border-radius:3px;background:radial-gradient(circle at 50% 55%,#3fb4e6 0%,#1a5c86 35%,#0e1c2a 75%)}
.cloud-card{left:751px;top:34px;width:235px;height:331px;border-radius:3px;background:var(--card-dark);color:#fff;padding:20px 18px}
.cloud-art{left:880px;top:16px;width:100px;height:68px;border-radius:40px 40px 10px 10px;background:linear-gradient(180deg,#bfe6ff,#2a79d6)}
.cloud-card .head{font-size:26px}
.cloud-card .intro{font-size:10px;line-height:11.5px;margin:8px 0 6px}
.ticks{list-style:none}
.ticks li{position:relative;padding-left:14px;margin-bottom:6px}
.ticks li b{display:block;font-weight:400;font-size:11px;line-height:13px}
.ticks li span{display:block;font-size:9.2px;line-height:11px;margin-top:2px}
.ticks li svg{position:absolute;left:0;top:3px}
.cloud-card .ticks b{color:var(--cyan)}
.cyber-person{left:735px;top:350px;width:277px;height:365px;background:linear-gradient(160deg,#f3f3f3 0%,#d9d4cf 45%,#8a8d92 100%)}
.cyber-title{left:533px;top:398px;font-size:28px;color:var(--cyan)}
.cyber-intro{left:533px;top:437px;width:185px;font-size:10px;line-height:11.5px}
.cyber-list{left:533px;top:482px;width:195px;list-style:none}
.cyber-list li{position:relative;padding-left:25px;margin-bottom:9px}
.cyber-list li b{display:block;font-weight:400;font-size:10.8px;line-height:13px}
.cyber-list li span{display:block;font-size:9.2px;line-height:11px;color:var(--ink-soft);margin-top:3px}
.cyber-list li svg{position:absolute;left:0;top:1px}

/* back spread */
.office-photo{left:0;top:0;width:506px;height:715px;background:linear-gradient(120deg,#4a4a4a 0%,#9c9c9c 35%,#e2e2e2 70%,#f5f5f5 100%)}
.ghost-back{left:-2px;top:598px;font-family:"Oswald",sans-serif;font-weight:700;font-size:140px;line-height:1;color:rgba(255,255,255,.35);white-space:nowrap;letter-spacing:-3px}
.consult-card{left:236px;top:35px;width:234px;height:309px;background:var(--cyan);padding:18px 18px}
.consult-card .head{font-size:27px;color:var(--ink)}
.consult-card .intro{font-size:9.8px;line-height:11.5px;margin:14px 0 9px}
.consult-card .ticks li{margin-bottom:7px}
.consult-card .ticks b{color:var(--ink)}
.consult-card .ticks span{color:#12507a}
.why-title{left:539px;top:50px;font-size:32px;line-height:32px}
.why-art{left:742px;top:23px;width:196px;height:129px;border-radius:50%;background:radial-gradient(circle,#5aa8ff 0%,#1d5fc4 35%,#e9eef5 62%,#fff 80%)}
.qmark{left:670px;top:84px;font-family:"Oswald",sans-serif;font-weight:700;font-size:70px;line-height:1;color:var(--cyan-deep)}
.feature{position:absolute;width:210px}
.feature svg{display:block}
.feature .head{font-size:21px;line-height:23px;margin-top:8px;letter-spacing:-.5px}
.feature p{font-size:9.5px;line-height:11.4px;color:var(--ink-soft);margin-top:10px}
.col-rule{position:absolute;left:757px;width:1px;background:#555}
.team-photo{left:536px;top:509px;width:445px;height:183px;background:radial-gradient(circle at 70% 50%,#2d6aa8 0%,#0f2f55 50%,#061426 100%)}
.team-brand{left:560px;top:537px;width:150px}
.team-brand .brand-name{color:#fff;font-size:21px}
</style>
</head>
<body>

<!-- Cover spread: contact panel and front cover -->
<section class="spread spread--cover">
  <div class="ph skyline" role="img" aria-label="Blue city skyline silhouette along the bottom of the spread"></div>
  <div class="abs ghost-name">Korvalith</div>

  <h3 class="abs touch-title center">Get in Touch</h3>
  <p class="abs touch-copy center">Discover how Korvalith can transform your IT landscape and drive your business forward. Contact us today to learn more about our services and how we can help you achieve your goals.</p>

  <div class="ph net-globe" role="img" aria-label="Sphere wrapped in a blue network of connected nodes"></div>

  <h3 class="abs contact-title center">Contact Us</h3>
  <ul class="abs contact-list">
    <li><svg width="10" height="12" viewBox="0 0 10 12"><path d="M1 0 L9 7 L5 7 L7 12 L5 12 L3 8 L1 10Z" fill="#1cb8f2"/></svg>korvalith.co.uk</li>
    <li><svg width="14" height="11" viewBox="0 0 14 11"><rect x="0" y="0" width="14" height="11" rx="1" fill="#1f1f1f"/><path d="M1 1 L7 6 L13 1" stroke="#fff" stroke-width="1.4" fill="none"/></svg>hello@korvalith.co.uk</li>
    <li><svg width="13" height="13" viewBox="0 0 13 13"><path d="M2 0 L5 3 L3.6 5 Q5 8 8 9.4 L10 8 L13 11 L11 13 Q4 12 0 2Z" fill="#1cb8f2"/></svg>+44 20 5550 1847</li>
    <li><svg width="10" height="14" viewBox="0 0 10 14"><path d="M5 0 A5 5 0 0 1 10 5 C10 9 5 14 5 14 C5 14 0 9 0 5 A5 5 0 0 1 5 0Z" fill="#1f1f1f"/><circle cx="5" cy="5" r="1.8" fill="#fff"/></svg>48 Harbour Row, Northgate<br>Park, London, UK</li>
  </ul>
  <div class="abs follow">Follow Us <span class="dot blue"></span><span class="dot"></span><span class="dot"></span></div>

  <div class="abs brand">
    <div class="brand-name">KORVALITH</div>
  </div>
  <div class="ph corner-globe" role="img" aria-label="Sphere with blue network nodes at the corner"></div>

  <h1 class="abs head cover-title center"><span>Korvalith</span><span>IT <span class="cyan" style="display:inline">Services</span></span></h1>
  <p class="abs tagline center">Empowering Your Business</p>
  <div class="abs tag-band">with Cutting-Edge IT Solutions</div>
</section>

<!-- Inside spread: about, services, cloud, cybersecurity -->
<section class="spread spread--inside">
  <h2 class="abs head about-title">About<br><span class="cyan">Korvalith</span></h2>
  <p class="abs about-copy">At Korvalith, we are dedicated to providing top-tier IT services that drive efficiency, innovation, and growth for your business. With a commitment to excellence and a team of highly skilled professionals, we offer a comprehensive suite of solutions tailored to meet the unique needs of our clients.</p>
  <div class="ph about-frame"></div>
  <div class="ph about-photo" role="img" aria-label="Support agents with headsets working at laptops"></div>

  <h2 class="abs head services-title"><span class="cyan">Our</span><br>Services</h2>
  <div class="abs rule-v" style="left:132px;top:291px;height:40px"></div>
  <p class="abs managed">Managed<br>IT Services</p>
  <div class="abs rule-v" style="left:242px;top:285px;height:46px"></div>
  <p class="abs managed-copy">Our Managed IT Services provide proactive monitoring and management of your IT infrastructure, ensuring maximum uptime &amp; reliability.</p>

  <div class="svc blue" style="left:29px;top:372px">
    <svg width="18" height="18" viewBox="0 0 18 18"><circle cx="9" cy="9" r="7" fill="none" stroke="#0677ba" stroke-width="1.6"/><path d="M9 4 V9 L12 11" stroke="#0677ba" stroke-width="1.6" fill="none"/></svg>
    <h4>24/7 Network<br>Monitoring</h4>
    <p>Continuous monitoring to detect and resolve issues before they impact your business.</p>
  </div>
  <div class="abs mid-brand"><div class="brand-name">KORVALITH</div></div>
  <div class="svc" style="left:338px;top:372px">
    <svg width="18" height="18" viewBox="0 0 18 18"><path d="M3 10 V8 A6 6 0 0 1 15 8 V10" fill="none" stroke="#0677ba" stroke-width="1.8"/><rect x="2" y="9" width="3" height="5" rx="1" fill="#0677ba"/><rect x="13" y="9" width="3" height="5" rx="1" fill="#0677ba"/><circle cx="9" cy="9" r="3" fill="#0677ba"/></svg>
    <h4>Helpdesk<br>Support</h4>
    <p>Responsive and knowledgeable support team available round the clock.</p>
  </div>
  <div class="svc" style="left:101px;top:531px">
    <svg width="20" height="18" viewBox="0 0 20 18"><circle cx="7" cy="5" r="4" fill="#0677ba"/><path d="M0 17 A7 7 0 0 1 14 17Z" fill="#0677ba"/><circle cx="16" cy="12" r="3" fill="none" stroke="#0677ba" stroke-width="2"/></svg>
    <h4>IT Asset<br>Management</h4>
    <p>Comprehensive tracking and management of your IT assets.</p>
  </div>
  <div class="svc blue" style="left:267px;top:531px">
    <svg width="18" height="18" viewBox="0 0 18 18"><path d="M3 9 A6 6 0 0 1 14 5 M15 9 A6 6 0 0 1 4 13" fill="none" stroke="#0677ba" stroke-width="1.8"/><path d="M14 1 V5 H10 M4 17 V13 H8" fill="none" stroke="#0677ba" stroke-width="1.8"/></svg>
    <h4>Patch<br>Management</h4>
    <p>Regular updates and patches to keep your systems secure and up-to-date.</p>
  </div>
  <svg class="arrow" style="left:48px;top:564px" width="32" height="26" viewBox="0 0 32 26"><path d="M2 4 Q4 14 18 14 V8 L30 17 L18 26 V20 Q4 20 2 4Z" fill="#1cb8f2"/></svg>
  <svg class="arrow" style="left:422px;top:564px" width="32" height="26" viewBox="0 0 32 26"><path d="M30 4 Q28 14 14 14 V8 L2 17 L14 26 V20 Q28 20 30 4Z" fill="#1cb8f2"/></svg>

  <div class="ph cloud-photo" role="img" aria-label="Hand holding a phone with glowing cloud icons rising from the screen"></div>
  <div class="ph cloud-card">
    <h2 class="head"><span class="cyan">Cloud</span><br>Solutions</h2>
    <p class="intro">Embrace the power of the cloud with our scalable and secure cloud solutions. Our offerings include:</p>
    <ul class="ticks">
      <li><svg width="9" height="8" viewBox="0 0 9 8"><path d="M1 4 L3.5 6.5 L8 1" stroke="#fff" stroke-width="1.5" fill="none"/></svg><b>Cloud Migration</b><span>Seamless transition of your applications and data to the cloud.</span></li>
      <li><svg width="9" height="8" viewBox="0 0 9 8"><path d="M1 4 L3.5 6.5 L8 1" stroke="#fff" stroke-width="1.5" fill="none"/></svg><b>Cloud Hosting</b><span>Reliable and scalable hosting solutions to meet your growing needs.</span></li>
      <li><svg width="9" height="8" viewBox="0 0 9 8"><path d="M1 4 L3.5 6.5 L8 1" stroke="#fff" stroke-width="1.5" fill="none"/></svg><b>Backup &amp; Disaster Recovery</b><span>Robust backup and recovery solutions to ensure business continuity.</span></li>
      <li><svg width="9" height="8" viewBox="0 0 9 8"><path d="M1 4 L3.5 6.5 L8 1" stroke="#fff" stroke-width="1.5" fill="none"/></svg><b>Software as a Service <span style="display:inline;color:#fff;font-size:11px">(SaaS)</span></b><span>Access to the latest software applications without the hassle of maintenance.</span></li>
    </ul>
  </div>
  <div class="ph cloud-art" role="img" aria-label="Glowing blue cloud above a server stack"></div>

  <div class="ph cyber-person" role="img" aria-label="Man in glasses and a grey sweater holding a tablet"></div>
  <h2 class="abs head cyber-title">Cybersecurity</h2>
  <p class="abs cyber-intro">Protect your business from evolving threats with our comprehensive cybersecurity services. We offer:</p>
  <ul class="abs cyber-list">
    <li><svg width="13" height="13" viewBox="0 0 13 13"><circle cx="8" cy="5" r="4" fill="none" stroke="#1f1f1f" stroke-width="1.4"/><path d="M5 8 L1 12" stroke="#1f1f1f" stroke-width="1.6"/></svg><b class="cyan">Threat Detection &amp; Response</b><span>Advanced threat monitoring and response to safeguard your data.</span></li>
    <li><svg width="13" height="13" viewBox="0 0 13 13"><circle cx="6.5" cy="6.5" r="6" fill="#1f1f1f"/><rect x="5.7" y="3" width="1.6" height="5" fill="#fff"/></svg><b>Security Audits &amp; Assessments</b><span>Thorough evaluations to identify and mitigate vulnerabilities.</span></li>
    <li><svg width="12" height="13" viewBox="0 0 12 13"><path d="M6 0 L12 2 V6 Q12 11 6 13 Q0 11 0 6 V2Z" fill="#1f1f1f"/><path d="M3 6.5 L5.3 8.6 L9 4.5" stroke="#fff" stroke-width="1.4" fill="none"/></svg><b class="cyan">Endpoint Protection</b><span>Robust security solutions for all your devices.</span></li>
    <li><svg width="13" height="13" viewBox="0 0 13 13"><path d="M2 6.5 A4.5 4.5 0 0 1 10 3.5 M11 6.5 A4.5 4.5 0 0 1 3 9.5" fill="none" stroke="#1f1f1f" stroke-width="1.4"/><path d="M4.5 6.5 L6 8 L8.5 5" stroke="#1f1f1f" stroke-width="1.3" fill="none"/></svg><b>Compliance &amp; Regulatory Services</b><span>Ensure adherence to industry standards and regulations.</span></li>
  </ul>
</section>

<!-- Back spread: consulting and why choose -->
<section class="spread spread--back">
  <div class="ph office-photo" role="img" aria-label="Bright monochrome office with a desktop computer and plants"></div>
  <div class="abs ghost-back">Korvalith</div>
  <div class="ph consult-card">
    <h2 class="head">IT Consulting</h2>
    <p class="intro">Leverage our expertise to drive your IT strategy and achieve your business goals. Our consulting services include:</p>
    <ul class="ticks">
      <li><svg width="9" height="8" viewBox="0 0 9 8"><path d="M1 4 L3.5 6.5 L8 1" stroke="#1f1f1f" stroke-width="1.5" fill="none"/></svg><b>IT Strategy &amp; Planning</b><span>Strategic guidance to align your IT initiatives with your business objectives.</span></li>
      <li><svg width="9" height="8" viewBox="0 0 9 8"><path d="M1 4 L3.5 6.5 L8 1" stroke="#1f1f1f" stroke-width="1.5" fill="none"/></svg><b>Technology Assessments</b><span>In-depth evaluations to optimize your IT infrastructure.</span></li>
      <li><svg width="9" height="8" viewBox="0 0 9 8"><path d="M1 4 L3.5 6.5 L8 1" stroke="#1f1f1f" stroke-width="1.5" fill="none"/></svg><b>Project Management</b><span>Expert management of IT projects from inception to completion.</span></li>
      <li><svg width="9" height="8" viewBox="0 0 9 8"><path d="M1 4 L3.5 6.5 L8 1" stroke="#1f1f1f" stroke-width="1.5" fill="none"/></svg><b>Business Continuity Planning</b><span>Strategies to ensure your business remains operational during disruptions.</span></li>
    </ul>
  </div>

  <h2 class="abs head why-title">Why<br><span class="cyan">Choose</span><br>Korvalith</h2>
  <div class="abs qmark">?</div>
  <div class="ph why-art" role="img" aria-label="Blue globe surrounded by connected laptops"></div>

  <div class="col-rule" style="top:198px;height:124px"></div>
  <div class="col-rule" style="top:370px;height:120px"></div>

  <div class="feature" style="left:539px;top:172px">
    <svg width="20" height="18" viewBox="0 0 20 18"><path d="M2 8 H5 V18 H2Z M6 8 L10 1 Q12 1 11 6 H16 Q18 6 17 9 L15 17 H6Z" fill="#1cb8f2"/></svg>
    <h3 class="head">Expertise and<br><span class="cyan">Experience</span></h3>
    <p>With years of experience in the IT industry, our team possesses the knowledge and skills to tackle any challenge. We stay abreast of the latest technological advancements to provide you with cutting-edge solutions.</p>
  </div>
  <div class="feature" style="left:780px;top:172px">
    <svg width="20" height="18" viewBox="0 0 20 18"><circle cx="10" cy="9" r="8" fill="none" stroke="#1f1f1f" stroke-width="1.6"/><circle cx="10" cy="7" r="3" fill="#1f1f1f"/><path d="M5 14 Q10 9 15 14" fill="#1f1f1f"/></svg>
    <h3 class="head">Customer-Centric<br><span class="cyan">Approach</span></h3>
    <p>We prioritize our clients' needs and work closely with them to deliver customized solutions that drive success. Our client centric approach ensures that we are always aligned with your business goals.</p>
  </div>
  <div class="feature" style="left:539px;top:342px">
    <svg width="18" height="20" viewBox="0 0 18 20"><path d="M9 0 L18 3 V9 Q18 17 9 20 Q0 17 0 9 V3Z" fill="#1f1f1f"/><path d="M5 10 L8 13 L13 7" stroke="#fff" stroke-width="1.8" fill="none"/></svg>
    <h3 class="head">Proactive<br><span class="cyan">Support</span></h3>
    <p>Our proactive support model ensures that potential issues are identified and resolved before they can impact your operations. We are committed to maintaining the highest levels of service availability and performance.</p>
  </div>
  <div class="feature" style="left:780px;top:342px">
    <svg width="18" height="20" viewBox="0 0 18 20"><circle cx="9" cy="8" r="6" fill="none" stroke="#1cb8f2" stroke-width="1.8"/><rect x="6" y="15" width="6" height="4" rx="1" fill="#1cb8f2"/><circle cx="9" cy="8" r="2" fill="#1cb8f2"/></svg>
    <h3 class="head">Comprehensive<br><span class="cyan">Solutions</span></h3>
    <p>From managed services to cybersecurity, we offer a comprehensive suite of IT solutions designed to meet the diverse needs of your business. Our holistic approach ensures that all aspects of your IT infrastructure are covered.</p>
  </div>

  <div class="ph team-photo" role="img" aria-label="Support engineer with a headset in a dark blue operations room"></div>
  <div class="abs team-brand"><div class="brand-name">KORVALITH</div></div>
</section>

</body>
</html>
```